Business Cards - Brightpath Horizon

need to design unique business card for my mortgage business. I need to design credit card style business card for my business or any unique idea that you might have

Target Market(s)

Home Loan customers

Industry/Entity Type

Mortgage Brokerage

Contact Information for Business Card

please design credit card style or very unique style business card

Colors

Designer to choose colors to be used in the design.

Requirements
Must have
• Name
• position
• Phone number
• fax number
• email address
• website address
• social media address
• All above fields will be provided once design in finalised

```html
<!DOCTYPE html>
<html lang="en">
<head>
<meta charset="utf-8">
<title>Brightpath Horizon – Business Cards</title>
<link rel="stylesheet" href="https://fonts.googleapis.com/css2?family=Work+Sans:wght@400;500&display=swap">
<style>
  :root {
    --page-bg: #1b1b1b;
    --card-bg: #2a2a2a;
    --edge-blue: #2ba6e2;
    --brand-blue: #2f4fb8;
    --name-blue: #1e63c4;
    --accent-orange: #f0901e;
    --text-light: #f2f2f2;
    --emboss-grey: #8a8a8a;
    --icon-blue: #2458b8;
  }
  * { margin: 0; padding: 0; box-sizing: border-box; }
  html, body { width: 1200px; height: 900px; overflow: hidden; }
  body {
    background: radial-gradient(ellipse at 60% 20%, #333 0%, var(--page-bg) 70%);
    font-family: "Work Sans", Arial, sans-serif;
    display: flex; flex-direction: column; align-items: center; justify-content: center;
    gap: 44px;
  }
  .card {
    position: relative;
    width: 760px; height: 380px;
    background: var(--card-bg);
    border-bottom: 9px solid var(--edge-blue);
    box-shadow: 0 20px 40px rgba(0,0,0,.55);
  }
  /* front */
  .card-front { display: flex; align-items: center; justify-content: center; }
  .front-mark { display: flex; align-items: center; gap: 16px; }
  .front-mark .brand-square { width: 26px; height: 26px; background: var(--emboss-grey); flex: none; }
  .front-name {
    font-weight: 500; font-size: 52px; letter-spacing: 1px;
    color: var(--emboss-grey); white-space: nowrap;
  }
  /* back */
  .card-back { display: flex; align-items: center; }
  .back-brand { width: 380px; padding: 0 24px; display: flex; justify-content: center; }
  .back-mark { display: flex; align-items: center; gap: 12px; }
  .back-mark .brand-square { width: 18px; height: 18px; background: var(--brand-blue); flex: none; }
  .back-name {
    font-weight: 500; font-size: 30px; color: var(--brand-blue);
    letter-spacing: .5px; white-space: nowrap;
  }
  .divider { width: 3px; height: 230px; background: var(--accent-orange); flex: none; }
  .contact { padding-left: 40px; color: var(--text-light); }
  .person-name { font-size: 26px; font-weight: 500; color: var(--name-blue); letter-spacing: 1.5px; text-transform: uppercase; }
  .person-role { font-size: 18px; letter-spacing: 1px; margin-top: 2px; }
  .address { font-size: 17px; line-height: 1.35; margin-top: 22px; letter-spacing: .5px; }
  .contact-list { list-style: none; margin-top: 20px; }
  .contact-list li { display: flex; align-items: center; gap: 16px; font-size: 17px; letter-spacing: .5px; line-height: 1.6; white-space: nowrap; }
  .contact-list svg { width: 16px; height: 16px; fill: var(--icon-blue); flex: none; }
</style>
</head>
<body>
  <section class="card card-front">
    <div class="front-mark">
      <span class="brand-square"></span>
      <span class="front-name">Brightpath Horizon</span>
    </div>
  </section>

  <section class="card card-back">
    <div class="back-brand">
      <div class="back-mark">
        <span class="brand-square"></span>
        <span class="back-name">Brightpath Horizon</span>
      </div>
    </div>
    <div class="divider"></div>
    <div class="contact">
      <p class="person-name">Daniel Archer</p>
      <p class="person-role">FOUNDER</p>
      <p class="address">48 Linden Crescent,<br>Toronto ON M4K 2B7</p>
      <ul class="contact-list">
        <li><svg viewBox="0 0 16 16" aria-hidden="true"><path d="M4 1h8a1 1 0 0 1 1 1v12a1 1 0 0 1-1 1H4a1 1 0 0 1-1-1V2a1 1 0 0 1 1-1zm1 2v9h6V3z"/></svg>(555) 014-2290</li>
        <li><svg viewBox="0 0 16 16" aria-hidden="true"><path d="M4 1h8v4H4zM2 6h12a1 1 0 0 1 1 1v5h-3v3H4v-3H1V7a1 1 0 0 1 1-1zm3 5v3h6v-3z"/></svg>(555) 014-7731</li>
        <li><svg viewBox="0 0 16 16" aria-hidden="true"><path d="M1 3h14v10H1zm1.5 1.2V5l5.5 4 5.5-4v-.8z"/></svg>daniel@brightpathhorizon.com</li>
        <li><svg viewBox="0 0 16 16" aria-hidden="true"><circle cx="8" cy="8" r="7"/></svg>brightpathhorizon.com</li>
      </ul>
    </div>
  </section>
</body>
</html>
```